10 Labels for Wild Bird Food

Label Design Request for New Products
We are excited to announce the launch of 10 new products and are seeking vibrant, fun, and colorful labels to match their energy. Each label should measure 6 x 4 inches (152.4mm x 101.6mm) and must feature our brand logo. Additionally, please include all the necessary information as detailed in the attached Word document.

Let's make our products stand out on the shelves with eye-catching designs!

Target Market(s)

Wild Bird Food Buyers

Requirements
Must have
• Logo

```html
<!DOCTYPE html>
<html lang="en">
<head>
<meta charset="UTF-8">
<title>No Mess Mix – Bird Food Label</title>
<link rel="stylesheet" href="https://fonts.googleapis.com/css2?family=Barlow+Condensed:wght@400;500;600;700&family=Chewy&family=Fredoka:wght@600&display=swap">
<style>
  :root {
    --border-green: #8cc34a;
    --teal: #1f8f86;
    --sky: #4ab9d9;
    --ink: #111111;
    --warn-red: #e3262b;
    --leaf: #5aa83a;
    --leaf-dark: #2f7a3a;
    --paper: #ffffff;
  }
  * { margin: 0; padding: 0; box-sizing: border-box; }
  html, body { width: 1200px; height: 800px; overflow: hidden; background: var(--paper); }
  .label {
    position: relative;
    width: 1200px; height: 800px;
    background: var(--paper);
    font-family: "Barlow Condensed", sans-serif;
    color: var(--ink);
  }
  .label-frame {
    position: absolute; inset: 10px;
    border: 3px solid var(--border-green);
    border-radius: 34px;
  }

  /* left column */
  .heading {
    font-family: "Chewy", sans-serif; font-weight: 400;
    color: var(--teal); text-align: center;
    font-size: 27px; line-height: 40px; white-space: nowrap;
  }
  .body-copy { font-size: 20px; line-height: 30px; font-weight: 400; }
  .body-copy .line { display: block; white-space: nowrap; text-align: justify; text-align-last: justify; }
  .body-copy .line.last { text-align-last: left; }

  .intro-heading { position: absolute; left: 28px; top: 20px; width: 282px; }
  .intro-copy { position: absolute; left: 28px; top: 138px; width: 281px; }
  .usage-heading { position: absolute; left: 33px; top: 379px; width: 268px; line-height: 40px; }
  .usage-copy { position: absolute; left: 33px; top: 416px; width: 268px; }

  .contact { position: absolute; left: 33px; top: 596px; font-size: 23px; line-height: 33.5px; }
  .contact dt { font-weight: 700; }
  .contact dd { font-weight: 400; }

  /* brand */
  .brand { position: absolute; left: 494px; top: 56px; display: flex; align-items: center; gap: 12px; }
  .brand-dot { width: 46px; height: 46px; border-radius: 50%; background: var(--teal); }
  .brand-name {
    font-family: "Chewy", sans-serif; font-weight: 400;
    color: var(--teal); font-size: 38px; line-height: 36px; white-space: nowrap;
  }

  /* product name */
  .product-title {
    position: absolute; left: 400px; top: 150px; width: 440px;
    font-family: "Fredoka", sans-serif; font-weight: 600;
    color: var(--sky); text-align: center;
    font-size: 104px; line-height: 114px; letter-spacing: -1px;
  }
  .product-title span { display: block; white-space: nowrap; }

  .scene {
    position: absolute; left: 313px; top: 377px; width: 597px; height: 400px;
    border-radius: 48% 48% 40% 40% / 55% 55% 30% 30%;
    background: radial-gradient(ellipse at 55% 40%, #7cc24a 0%, var(--leaf) 45%, var(--leaf-dark) 100%);
  }

  /* right column */
  .notice { position: absolute; width: 170px; text-align: center; font-weight: 700; font-size: 25px; line-height: 22px; }
  .notice svg { display: block; margin: 0 auto; }
  .notice-human { left: 996px; top: 20px; }
  .notice-human svg { margin-bottom: 8px; }
  .notice-nuts { left: 998px; top: 190px; }
  .notice-nuts svg { margin-bottom: 6px; }

  .facts { position: absolute; right: 37px; top: 351px; width: 320px; text-align: right; }
  .facts-heading { color: var(--teal); font-weight: 500; font-size: 26px; line-height: 32px; }
  .ingredients { font-weight: 600; font-size: 25px; line-height: 28px; }
  .spec { font-weight: 600; font-size: 25px; line-height: 31px; }
  .ingredients + .spec { margin-top: 7px; }

  .fill-label { position: absolute; right: 218px; font-size: 23px; line-height: 30px; white-space: nowrap; }
  .fill-box { position: absolute; left: 991px; width: 172px; height: 38px; border: 2px solid var(--ink); }
  .expiry-label { top: 544px; }
  .expiry-box { top: 539px; }
  .batch-label { top: 585px; }
  .batch-box { top: 585px; }
</style>
</head>
<body>
<main class="label">
  <div class="label-frame"></div>

  <h2 class="heading intro-heading">Enjoy a Clean and Vibrant<br>Garden with our<br>Nutritious No Mess Mix!</h2>
  <p class="body-copy intro-copy">
    <span class="line">Invite a diverse array of beautiful birds to</span>
    <span class="line">your garden without the hassle of leftover</span>
    <span class="line">shells and debris with our No Mess Mix 5L</span>
    <span class="line">Bag. This premium bird food is specially</span>
    <span class="line">formulated to provide a nutritious,</span>
    <span class="line">easy-to-eat blend that leaves no waste,</span>
    <span class="line">ensuring your garden remains clean and</span>
    <span class="line last">your feathered visitors are well-fed.</span>
  </p>

  <h3 class="heading usage-heading">Easy to Use:</h3>
  <p class="body-copy usage-copy">
    <span class="line">Fill your bird feeders, place on bird tables,</span>
    <span class="line">or scatter on the ground to create an</span>
    <span class="line">inviting and clean feeding space for birds.</span>
    <span class="line">Watch as they flock to your garden,</span>
    <span class="line">bringing vibrant colors and joyful chirping</span>
    <span class="line last">to your outdoor area.</span>
  </p>

  <dl class="contact">
    <dt>Address:</dt>
    <dd>Marlow Trading, Kestrel Court</dd>
    <dd>Business Park, Alderbury, SP5 3LN</dd>
    <dt>Contact:</dt>
    <dd>Sales@marlowtrading.co.uk</dd>
  </dl>

  <div class="brand">
    <span class="brand-dot"></span>
    <span class="brand-name">peckish<br>perch</span>
  </div>

  <h1 class="product-title"><span>No Mess</span><span>Mix</span></h1>

  <div class="scene" role="img" aria-label="Illustration of a garden scene with a blue bird on a post, a leafy tree, a small bird house, flowers and stepping stones"></div>

  <div class="notice notice-human">
    <svg width="104" height="104" viewBox="0 0 104 104" aria-hidden="true">
      <circle cx="52" cy="52" r="45" fill="none" stroke="var(--warn-red)" stroke-width="12"/>
      <line x1="20" y1="84" x2="84" y2="20" stroke="var(--warn-red)" stroke-width="12"/>
    </svg>
    Not for human<br>consumption
  </div>

  <div class="notice notice-nuts">
    <svg width="104" height="104" viewBox="0 0 104 104" aria-hidden="true">
      <circle cx="52" cy="52" r="45" fill="none" stroke="var(--border-green)" stroke-width="9"/>
      <g transform="rotate(-45 52 52)">
        <path d="M52 22c12 0 16 8 13 16-2 5-2 7 0 12 4 10-1 24-13 24s-17-14-13-24c2-5 2-7 0-12-3-8 1-16 13-16z" fill="var(--teal)"/>
      </g>
    </svg>
    May Contain<br>Nuts
  </div>

  <section class="facts">
    <h3 class="facts-heading">Composition:</h3>
    <p class="ingredients">Oat Meal, Cut Maize, Peanut<br>Granules, Sunflower Hearts, Naked<br>Oats, Raisins, Soya Bean Oil</p>
    <p class="spec">Net Weight: 3200g</p>
    <p class="spec">SKU: PP28</p>
  </section>

  <span class="fill-label expiry-label">Expiry Date:</span>
  <div class="fill-box expiry-box"></div>
  <span class="fill-label batch-label">Batch:</span>
  <div class="fill-box batch-box"></div>
</main>
</body>
</html>
```